New business card/stationary for a consulting company

I am looking for a clean and very professional looking business card for my consulting company as well as corresponding stationary. I am uploading our logo. I like simple and powerful for the feel. No graphics but I am open on everything else. Below is my contact information but would like the final to be in a version I can add my employees information into and print. Thank you.

Daniel Whitcombe
dan@ferncliffadvisory.com
2870 North 9th Avenue, Summit Floor, Elm Ridge, Illinois 60531
www.ferncliffadvisory.com

Industry/Entity Type

Consulting

Contact Information for Business Card

Daniel Whitcombe
dan@ferncliffadvisory.com
www.ferncliffadvisory.com

Font styles to use
Serif
Sans Serif

Requirements
Must have
• Our logo and the business card details.
Nice to have
• our website www.ferncliffadvisory.com

```html
<!DOCTYPE html>
<html lang="en">
<head>
<meta charset="utf-8">
<title>Ferncliff Advisory – Business Card</title>
<link href="https://fonts.googleapis.com/css2?family=Lato:wght@400;700&display=swap" rel="stylesheet">
<style>
  :root {
    --navy: #07076a;
    --white: #ffffff;
    --ink: #141414;
    --backdrop: #2b2b2b;
  }
  * { margin: 0; padding: 0; box-sizing: border-box; }
  html, body {
    width: 1200px;
    height: 900px;
    overflow: hidden;
    background: var(--backdrop);
    font-family: "Lato", Arial, sans-serif;
  }
  .canvas {
    position: relative;
    width: 1200px;
    height: 900px;
  }
  .card {
    position: absolute;
    left: 280px;
    width: 640px;
    height: 366px;
    overflow: hidden;
  }
  .card--front { top: 40px; background: var(--navy); }
  .card--back  { top: 480px; background: var(--white); }

  .brand {
    display: flex;
    align-items: center;
    gap: 14px;
    letter-spacing: 0.08em;
    text-transform: uppercase;
    font-weight: 400;
  }
  .brand__square { width: 22px; height: 22px; flex: none; }

  .card--front .brand {
    position: absolute;
    left: 0; right: 0; top: 160px;
    justify-content: center;
    color: var(--white);
    font-size: 32px;
  }
  .card--front .brand__square { background: var(--white); }

  .card--back .brand {
    position: absolute;
    left: 48px; top: 60px;
    color: var(--navy);
    font-size: 26px;
  }
  .card--back .brand__square { background: var(--navy); width: 18px; height: 18px; }

  .holder-name {
    position: absolute;
    left: 48px; top: 200px;
    color: var(--navy);
    font-size: 26px;
    font-weight: 400;
    letter-spacing: -0.01em;
    text-transform: uppercase;
  }
  .contact {
    position: absolute;
    left: 350px; top: 196px;
    color: var(--ink);
    font-size: 16px;
    line-height: 1.35;
  }
  .contact__address { margin-bottom: 10px; }
  .contact__line { display: flex; align-items: center; gap: 10px; }
  .contact__line svg { width: 15px; height: 15px; flex: none; }
  .card__band {
    position: absolute;
    left: 0; right: 0; bottom: 0;
    height: 14px;
    background: var(--navy);
  }
</style>
</head>
<body>
<main class="canvas">
  <section class="card card--front" aria-label="Card front">
    <div class="brand"><span class="brand__square"></span>Ferncliff Advisory</div>
  </section>

  <section class="card card--back" aria-label="Card back">
    <div class="brand"><span class="brand__square"></span>Ferncliff Advisory</div>
    <h1 class="holder-name">Daniel Whitcombe</h1>
    <div class="contact">
      <p class="contact__address">2870 North 9th Avenue<br>Summit Floor<br>Elm Ridge, Illinois 60531</p>
      <p class="contact__line">
        <svg viewBox="0 0 16 16" aria-hidden="true"><rect x="1" y="3" width="14" height="10" fill="var(--navy)"/><path d="M1 3 L8 9 L15 3" fill="none" stroke="#fff" stroke-width="1.2"/></svg>
        dan@ferncliffadvisory.com
      </p>
      <p class="contact__line">
        <svg viewBox="0 0 16 16" aria-hidden="true"><circle cx="8" cy="8" r="7" fill="var(--navy)"/><g fill="none" stroke="#fff" stroke-width="0.9"><ellipse cx="8" cy="8" rx="3" ry="7"/><line x1="1" y1="8" x2="15" y2="8"/><line x1="2.2" y1="4.5" x2="13.8" y2="4.5"/><line x1="2.2" y1="11.5" x2="13.8" y2="11.5"/></g></svg>
        www.ferncliffadvisory.com
      </p>
    </div>
    <div class="card__band"></div>
  </section>
</main>
</body>
</html>
```